Silver Meadow LLC business card

I help with the Marketing and Sales of various Natural, Organic, Eco Friendly and Healthy Main Stream products to Retail Corporate accounts as well as Independents and Distributors.I also highlight Private label items to these same Retail Corporate accounts.Cherish the Moments, Enjoy Life!

Speciality & Health Sales and Marketing

Target Market(s)

Men and Women

Industry/Entity Type

Business

Contact Information for Business Card

Silver Meadow, LLC
Janet Louise Verhagen
438 West Finch Lane
Ste 4-237
Phoenix, AZ 85047
602-555-0147
jverhagen@plumvale.net

Requirements
Must have
• Nice, femine font
Something in the background or on a side with a softness
Nice to have
• Cherish the Moments, Enjoy Life
Should not have
• Hardness

```html
<!DOCTYPE html>
<html lang="en">
<head>
<meta charset="utf-8">
<title>Silver Meadow LLC – Business Card</title>
<link rel="stylesheet" href="https://fonts.googleapis.com/css2?family=Cormorant+Garamond:ital,wght@0,500;0,600;1,500&family=Lato:wght@300;400&display=swap">
<style>
  :root {
    --backdrop: #3b322d;
    --card: #1d1b1d;
    --card-glow: #2e2a2e;
    --accent: #f08a52;
    --accent-soft: rgba(240, 138, 82, 0.16);
    --text-light: #f4efec;
    --text-soft: #dcd5d1;
    --silver: #cfcaca;
    --silver-soft: rgba(220, 214, 214, 0.12);
    --divider: rgba(255, 255, 255, 0.08);
  }
  * { margin: 0; padding: 0; box-sizing: border-box; }
  html, body {
    width: 1200px;
    height: 844px;
    overflow: hidden;
    background: var(--backdrop);
    font-family: "Lato", Arial, sans-serif;
  }
  .stage {
    position: relative;
    width: 1200px;
    height: 844px;
  }
  .card {
    position: absolute;
    top: 272px;
    width: 520px;
    height: 300px;
    border-radius: 12px;
    background: radial-gradient(ellipse at 60% 30%, var(--card-glow), var(--card) 72%);
    box-shadow: 0 16px 36px rgba(0, 0, 0, 0.4);
    overflow: hidden;
  }
  .card--front { left: 50px; }
  .card--back  { left: 630px; }

  /* Front side */
  .front-brand {
    position: absolute;
    left: 0;
    top: 0;
    width: 250px;
    height: 100%;
    display: flex;
    flex-direction: column;
    align-items: center;
    justify-content: center;
    gap: 14px;
    background: radial-gradient(circle at 50% 42%, var(--accent-soft), transparent 68%);
  }
  .front-divider {
    position: absolute;
    left: 250px;
    top: 30px;
    width: 1px;
    height: 240px;
    background: linear-gradient(transparent, var(--divider), transparent);
  }
  .brand-mark { display: block; }
  .brand-name {
    font-family: "Cormorant Garamond", Georgia, serif;
    font-weight: 600;
    font-size: 27px;
    letter-spacing: 0.5px;
    color: var(--accent);
    white-space: nowrap;
  }
  .contact {
    position: absolute;
    left: 272px;
    top: 46px;
    width: 236px;
    color: var(--text-light);
  }
  .contact__name {
    font-family: "Cormorant Garamond", Georgia, serif;
    font-size: 24px;
    font-weight: 600;
    line-height: 1.1;
    white-space: nowrap;
  }
  .contact__role {
    font-family: "Cormorant Garamond", Georgia, serif;
    font-style: italic;
    font-weight: 500;
    font-size: 16px;
    color: var(--accent);
    margin-top: 3px;
  }
  .contact__address {
    font-size: 12.5px;
    font-weight: 300;
    line-height: 1.5;
    color: var(--text-soft);
    margin-top: 14px;
  }
  .contact__lines {
    list-style: none;
    font-size: 12.5px;
    font-weight: 300;
    line-height: 1.6;
    color: var(--text-soft);
    margin-top: 12px;
  }
  .contact__label {
    color: var(--accent);
    display: inline-block;
    width: 20px;
    font-weight: 400;
  }

  /* Back side */
  .back-brand {
    position: absolute;
    inset: 0;
    display: flex;
    flex-direction: column;
    align-items: center;
    justify-content: center;
    gap: 18px;
    background: radial-gradient(circle at 50% 40%, var(--silver-soft), transparent 60%);
  }
  .back-brand .brand-name {
    font-size: 38px;
    color: var(--silver);
  }
</style>
</head>
<body>
<main class="stage">

  <section class="card card--front" aria-label="Business card front">
    <div class="front-brand">
      <svg class="brand-mark" width="76" height="76" viewBox="0 0 76 76" aria-hidden="true">
        <circle cx="38" cy="38" r="36" fill="var(--accent)"/>
      </svg>
      <span class="brand-name">Silver Meadow LLC</span>
    </div>
    <div class="front-divider"></div>
    <div class="contact">
      <p class="contact__name">Janet Louise Verhagen</p>
      <p class="contact__role">Managing Director</p>
      <p class="contact__address">438 West Finch Lane, Ste 4-237<br>Phoenix, AZ 85047</p>
      <ul class="contact__lines">
        <li><span class="contact__label">T:</span>602-555-0147</li>
        <li><span class="contact__label">E:</span>jverhagen@plumvale.net</li>
        <li><span class="contact__label">W:</span>www.plumvale.net</li>
      </ul>
    </div>
  </section>

  <section class="card card--back" aria-label="Business card back">
    <div class="back-brand">
      <svg class="brand-mark" width="92" height="92" viewBox="0 0 92 92" aria-hidden="true">
        <defs>
          <linearGradient id="silverFill" x1="0" y1="0" x2="1" y2="1">
            <stop offset="0" stop-color="#e4e0e0"/>
            <stop offset="1" stop-color="#9c9797"/>
          </linearGradient>
        </defs>
        <circle cx="46" cy="46" r="44" fill="url(#silverFill)"/>
      </svg>
      <span class="brand-name">Silver Meadow LLC</span>
    </div>
  </section>

</main>
</body>
</html>
```